Modern web-site for a game changer new health app!

We need a very clean UX / UI design for our company website that will be used to sell our brand to large corporations and their employees. If we find a good match, we'd need you to do the app design and some graphics for ongoing design needs.

For a first of its kind app developed at Brockwell University, making licensed holistic medicine accessible to everyday people through access and curation by democratizing holistic health.

Please read the details attached thoroughly and reach out if you have any questions. Many thanks!
Updates

I've updated our requirements to make it easier, please review new details in the PDF shared. Many thanks!

Final brief refinement just uploaded, much has been simplified with very clear guidelines, please update and apply. thanks much!

Target Market(s)

corporate employees and large C level corporate leaders

Industry/Entity Type

wellness

Number of Pages Required

4 page

Font styles to use
Other font styles liked:
• We need website design now and app and socials after, hoping the designer we choose now can work with us on a regular basis going forward

Requirements
Must have
• clean, modern, minimal rich
Nice to have
• some added touches to give a custom feel
Should not have
• pictures, natural looking images or shapes

```html
<!DOCTYPE html>
<html lang="en">
<head>
<meta charset="UTF-8">
<title>Omvela — Wellness for Everyone</title>
<link href="https://fonts.googleapis.com/css2?family=Montserrat:wght@500;600;700;800&family=Lato:wght@400;700&display=swap" rel="stylesheet">
<style>
:root{
  --orange-deep:#d05a08;
  --orange:#e67e0c;
  --gold:#f2aa0a;
  --ink:#111111;
  --text:#3a3a3a;
  --cream:#faebe3;
  --white:#ffffff;
  --footer:#000000;
  --hero-tone:#2b3a22;
  --sunset-tone:#e9a465;
  --photo-tone:#e4dcd4;
  --grad:linear-gradient(90deg,var(--gold),var(--orange-deep));
}
*{box-sizing:border-box;margin:0;padding:0}
html,body{width:1200px;height:3939px;overflow:hidden}
body{font-family:'Lato',sans-serif;color:var(--text);background:var(--white);position:relative}
.abs{position:absolute}
h1,h2,h3{font-family:'Montserrat',sans-serif}

/* header */
.topline{top:0;left:0;width:1200px;height:4px;background:var(--grad)}
.header{top:4px;left:0;width:1200px;height:85px;background:var(--white)}
.brand{left:110px;top:18px;font-family:'Montserrat',sans-serif;font-weight:800;font-size:38px;color:var(--orange);letter-spacing:1px;display:flex;align-items:center;gap:8px}
.brand-dot{width:12px;height:12px;border-radius:50%;background:var(--orange)}
.nav{right:112px;top:20px;display:flex;align-items:center;gap:40px;font-family:'Montserrat',sans-serif;font-weight:600;font-size:15px;color:var(--ink)}
.btn{display:inline-block;background:var(--grad);color:#fff;font-family:'Montserrat',sans-serif;font-weight:800;text-transform:uppercase;border-radius:6px}
.nav .btn{padding:14px 18px;font-size:15px;margin-left:-18px}

/* hero */
.hero{top:89px;left:0;width:1200px;height:600px;overflow:hidden}
.hero-photo{position:absolute;inset:0;background:var(--hero-tone)}
.hero-title{top:152px;left:0;width:1200px;text-align:center;color:#fff;font-size:55px;font-weight:800;letter-spacing:1px}
.hero-sub{top:228px;left:0;width:1200px;text-align:center;color:#fff;font-size:18px;line-height:31px}
.hero .btn{top:307px;left:525px;width:150px;height:47px;line-height:47px;text-align:center;font-size:15px}
.hero-arrow{width:28px;height:28px;border:1.5px solid #fff;border-radius:50%;top:268px;display:flex;align-items:center;justify-content:center}
.hero-wave{left:0;top:500px;width:1200px;height:190px}

/* steps */
.step{width:300px;text-align:center}
.step-ring{width:124px;height:124px;border:2px solid var(--orange);border-radius:50%;margin:0 auto;position:relative;display:flex;align-items:center;justify-content:center}
.step-core{width:92px;height:92px;border-radius:50%;background:#fcebd4;display:flex;align-items:center;justify-content:center}
.step-num{position:absolute;left:6px;bottom:-4px;width:30px;height:30px;border-radius:50%;background:var(--orange-deep);color:#fff;font-family:'Montserrat',sans-serif;font-weight:700;font-size:12px;line-height:26px;border:2px solid #fff}
.step h3{font-size:19px;font-weight:600;color:var(--ink);margin-top:26px}
.step p{font-size:14px;line-height:24px;margin-top:12px}
.step-arrow{width:110px;height:40px}

/* sections */
.cream{background:var(--cream);left:0;width:1200px}
.sec-title{left:0;width:1200px;text-align:center;font-size:31px;font-weight:600;color:var(--ink);letter-spacing:.5px}
.underline{width:78px;height:3px;background:var(--grad)}

/* services */
.card{width:228px;height:303px;background:#fff;border:2px solid #f2dccf;border-radius:10px;top:1336px;padding:12px}
.card-photo{width:100%;height:193px;border-radius:6px;background:var(--photo-tone)}
.card h3{font-size:16px;font-weight:600;color:var(--ink);text-align:center;line-height:27px;margin-top:20px}
.svc-arrow{width:30px;height:30px;border-radius:50%;top:1473px;display:flex;align-items:center;justify-content:center}

/* enterprise */
.ent-title{left:109px;top:1870px;font-size:31px;font-weight:600;color:var(--ink)}
.ent-lead{left:112px;top:1948px;font-size:16px;color:var(--ink);font-weight:700}
.ent-copy{left:110px;top:1990px;width:470px;font-size:15px;line-height:27px}
.ent-copy p+p{margin-top:26px}
.ent .btn{left:110px;top:2146px;width:277px;height:46px;line-height:46px;text-align:center;font-size:15px}
.ent-block{left:624px;top:1988px;width:298px;height:220px;background:var(--grad);border-radius:10px}
.ent-photo{left:639px;top:1865px;width:442px;height:328px;border-radius:10px;background:var(--sunset-tone)}

/* how it works */
.how-copy{left:150px;top:2494px;width:900px;text-align:center;font-size:15px;line-height:28px}
.how-step{width:260px;text-align:center}
.how-ring{width:102px;height:102px;border-radius:50%;background:var(--grad);margin:0 auto;display:flex;align-items:center;justify-content:center}
.how-inner{width:80px;height:80px;border-radius:50%;border:2px solid rgba(255,255,255,.8);display:flex;align-items:center;justify-content:center}
.how-step h3{font-size:16px;font-weight:600;color:var(--ink);line-height:27px;margin-top:22px}

/* testimonials */
.tcard{top:3063px;width:310px;height:328px;border:2.5px solid var(--gold);border-radius:10px;padding:24px 26px;background:#fff;box-shadow:0 6px 14px rgba(230,126,12,.12)}
.stars{color:var(--orange);font-size:15px;letter-spacing:2px}
.tcard p{font-size:14px;line-height:26px;text-align:justify;color:var(--ink);margin-top:10px;font-family:Arial,sans-serif}
.tcard hr{border:none;border-top:1.5px solid #bbb;margin-top:40px}
.person{display:flex;align-items:center;gap:16px;margin-top:24px}
.avatar{width:54px;height:54px;border-radius:50%;background:#cbbdb1}
.person b{display:block;font-family:'Montserrat',sans-serif;font-weight:600;font-size:18px;color:var(--ink)}
.person span{font-size:14px;font-family:Arial,sans-serif}

/* footer */
.footer{top:3494px;left:0;width:1200px;height:445px;background:var(--footer);color:#fff}
.f-head{top:73px;font-family:'Montserrat',sans-serif;font-weight:700;font-size:21px;color:#fff}
.links{left:98px;top:114px;list-style:none;font-size:15px;line-height:31px}
.links li{display:flex;align-items:center;gap:12px}
.socials{left:98px;top:312px;display:flex;gap:8px}
.socials span{width:30px;height:30px;border:1.5px solid #fff;border-radius:50%}
.vline{top:90px;width:0;height:240px;border-left:1px solid #888}
.contact{left:355px;top:110px;width:290px}
.ci{display:flex;gap:14px;padding-bottom:14px;border-bottom:1px dashed #aaa;margin-bottom:20px;width:240px}
.ci:last-child{border:none;width:290px}
.ci-icon{width:32px;height:32px;border-radius:50%;background:var(--grad);flex:none;display:flex;align-items:center;justify-content:center;margin-top:6px}
.ci b{display:block;font-size:18px;font-weight:700}
.ci span{font-size:16px;line-height:30px;white-space:nowrap}
.form{left:716px;top:102px;width:353px}
.field{height:40px;border:1.5px solid #fff;border-radius:3px;margin-bottom:13px;padding-left:12px;line-height:37px;font-size:14px}
.submit{height:38px;background:linear-gradient(90deg,var(--orange-deep),var(--gold));text-align:center;line-height:38px;font-weight:700;font-size:17px;border-radius:2px;margin-top:2px}
.f-rule{left:98px;top:387px;width:1004px;border-top:1px solid #aaa}
.copy{left:0;top:406px;width:1200px;text-align:center;font-size:14px}
</style>
</head>
<body>

<div class="abs topline"></div>
<header class="abs header">
  <div class="abs brand"><span class="brand-dot"></span>Omvela</div>
  <nav class="abs nav">
    <span>COMPLEMENTARY</span><span>ENTERPRISE</span><span>MEMBERS</span>
    <span class="btn">Get Started</span>
  </nav>
</header>

<section class="abs hero">
  <div class="hero-photo" role="img" aria-label="Close-up photograph of white flower buds among green leaves"></div>
  <h1 class="abs hero-title">WELLNESS FOR EVERYONE</h1>
  <p class="abs hero-sub">Modern Science meets Ancient Wisdom<br>Get 1 on 1 PHD care on US for personalized remedies</p>
  <span class="abs btn">Get Started</span>
  <div class="abs hero-arrow" style="left:36px"><svg width="12" height="12" viewBox="0 0 12 12"><path d="M8 2 4 6l4 4" stroke="#fff" stroke-width="1.6" fill="none"/></svg></div>
  <div class="abs hero-arrow" style="left:1129px"><svg width="12" height="12" viewBox="0 0 12 12"><path d="M4 2l4 4-4 4" stroke="#fff" stroke-width="1.6" fill="none"/></svg></div>
  <svg class="abs hero-wave" viewBox="0 0 1200 190" preserveAspectRatio="none">
    <defs><linearGradient id="wg" x1="0" x2="1"><stop offset="0" stop-color="#d05a08"/><stop offset="1" stop-color="#f2aa0a"/></linearGradient></defs>
    <path d="M0 105 C150 40 300 20 420 30 C560 45 650 120 800 120 C950 120 1080 95 1200 62 L1200 190 L0 190Z" fill="url(#wg)"/>
    <path d="M0 190 L0 135 C150 70 300 50 420 50 C560 55 650 140 800 140 C950 140 1080 130 1200 90 L1200 190Z" fill="#fff"/>
  </svg>
</section>

<!-- steps -->
<div class="abs step" style="left:92px;top:794px">
  <div class="step-ring"><div class="step-core"><svg width="40" height="40" viewBox="0 0 40 40" fill="none" stroke="#e67e0c" stroke-width="2.2"><circle cx="17" cy="10" r="4"/><path d="M11 30V20h12l3 6M8 32h24"/><circle cx="30" cy="10" r="3"/></svg></div><span class="step-num">01</span></div>
  <h3>Take Test</h3>
  <p>Sed ornare, turpis eu aliquet placerat,<br>nisi erat pharetra nunc, ac lacinia massa<br>urna ut diam.</p>
</div>
<svg class="abs step-arrow" style="left:352px;top:836px" viewBox="0 0 110 40"><path d="M2 22 C30 40 70 38 100 10" stroke="#111" stroke-width="2" fill="none"/><path d="M90 8l12 0-4 12" stroke="#111" stroke-width="2" fill="none"/></svg>
<div class="abs step" style="left:450px;top:794px">
  <div class="step-ring"><div class="step-core"><svg width="42" height="42" viewBox="0 0 42 42" fill="none" stroke="#e67e0c" stroke-width="2.2"><circle cx="14" cy="14" r="7"/><circle cx="28" cy="28" r="7"/><path d="M28 8a6 6 0 0 1 6 6M8 28a6 6 0 0 0 6 6"/></svg></div><span class="step-num">02</span></div>
  <h3>Get Matched with a Specialist</h3>
  <p>Sed ornare, turpis eu aliquet placerat,<br>nisi erat pharetra nunc, ac lacinia massa<br>urna ut diam.</p>
</div>
<svg class="abs step-arrow" style="left:732px;top:836px" viewBox="0 0 110 40"><path d="M2 22 C30 40 70 38 100 10" stroke="#111" stroke-width="2" fill="none"/><path d="M90 8l12 0-4 12" stroke="#111" stroke-width="2" fill="none"/></svg>
<div class="abs step" style="left:808px;top:794px">
  <div class="step-ring"><div class="step-core"><svg width="42" height="42" viewBox="0 0 42 42" fill="none" stroke="#e67e0c" stroke-width="2.2"><rect x="6" y="10" width="30" height="20" rx="2"/><path d="M2 34h38"/><circle cx="18" cy="18" r="3"/><path d="M13 27a5 5 0 0 1 10 0M26 15h6M26 20h6"/></svg></div><span class="step-num">03</span></div>
  <h3>Video Consult</h3>
  <p>Sed ornare, turpis eu aliquet placerat,<br>nisi erat pharetra nunc, ac lacinia massa<br>urna ut diam.</p>
</div>

<!-- services -->
<section class="abs cream" style="top:1151px;height:604px"></section>
<h2 class="abs sec-title" style="top:1240px">OUR SERVICES</h2>
<div class="abs underline" style="left:561px;top:1289px"></div>
<div class="abs svc-arrow" style="left:42px;background:#000"><svg width="14" height="14" viewBox="0 0 14 14"><path d="M12 7H3M7 3 3 7l4 4" stroke="#fff" stroke-width="2" fill="none"/></svg></div>
<div class="abs svc-arrow" style="left:1128px;background:var(--gold)"><svg width="14" height="14" viewBox="0 0 14 14"><path d="M2 7h9M7 3l4 4-4 4" stroke="#fff" stroke-width="2" fill="none"/></svg></div>
<div class="abs card" style="left:110px"><div class="card-photo" role="img" aria-label="Photo of a woman at a table with fruit and a supplement bottle"></div><h3>Personalized Custom<br>Supplements</h3></div>
<div class="abs card" style="left:360px"><div class="card-photo" role="img" aria-label="Photo of a woman taking a capsule with a glass of water"></div><h3>Gut, Hormone &amp;<br>Cellular Lab Tests</h3></div>
<div class="abs card" style="left:610px"><div class="card-photo" role="img" aria-label="Silhouette of a person meditating at sunset" style="background:var(--sunset-tone)"></div><h3>Free Yoga, Meditation &amp;<br>Health Essentials</h3></div>
<div class="abs card" style="left:860px"><div class="card-photo" role="img" aria-label="Photo of a holistic doctor in a clinic"></div><h3>1 on 1 with Holistic<br>Doctors</h3></div>

<!-- enterprise -->
<section class="ent">
  <h2 class="abs ent-title">SOLVIA FOR ENTERPRISE</h2>
  <div class="abs underline" style="left:109px;top:1921px"></div>
  <p class="abs ent-lead">We're all feeling a strain on our health these days</p>
  <div class="abs ent-copy">
    <p>Leaders of industry aren't accidental, they know employee<br>retention &amp; experience work in their favor.</p>
    <p>In these tumultuous times, Solvia brings much-needed relief<br>and benefits to teams that bring their all in return.</p>
  </div>
  <span class="abs btn">Solvia for Enterprise</span>
  <div class="abs ent-block"></div>
  <div class="abs ent-photo" role="img" aria-label="Photo of a woman in a yoga pose on a rock above a lake at sunset"></div>
</section>

<!-- how it works -->
<section class="abs cream" style="top:2315px;height:566px"></section>
<h2 class="abs sec-title" style="top:2408px">HOW IT WORKS</h2>
<div class="abs underline" style="left:561px;top:2457px"></div>
<p class="abs how-copy">Sign-up and get a full read of your unique constitution and what makes it thrive with a custom plan made one on one with your on-demand holistic Doctor/Educator.Unlimited texting to address your plan or any other concern you have about your health.</p>
<svg class="abs" style="left:340px;top:2590px" width="540" height="60" viewBox="0 0 540 60" fill="none" stroke="#222" stroke-width="1.4" stroke-dasharray="5 4"><path d="M7 50 C80 5 170 5 225 40"/><path d="M315 50 C380 5 470 5 530 40"/></svg>
<div class="abs how-step" style="left:173px;top:2606px">
  <div class="how-ring"><div class="how-inner"><svg width="40" height="40" viewBox="0 0 40 40" fill="#fff"><circle cx="17" cy="12" r="7"/><path d="M4 34c0-8 6-13 13-13 3 0 5 1 7 2-3 2-4 5-4 8 0 1 0 2 1 3Z"/><circle cx="29" cy="30" r="7" fill="none" stroke="#fff" stroke-width="2"/><path d="M29 26v8M25 30h8" stroke="#fff" stroke-width="2"/></svg></div></div>
  <h3>SIGN-UP</h3>
</div>
<div class="abs how-step" style="left:477px;top:2606px">
  <div class="how-ring"><div class="how-inner"><svg width="40" height="40" viewBox="0 0 40 40" fill="none" stroke="#fff" stroke-width="2.4"><rect x="11" y="5" width="20" height="26" rx="2"/><path d="M16 12h10M16 17h10M16 22h10M7 35h28"/></svg></div></div>
  <h3>GET A FULL READ OF YOUR<br>CONSTITUTION</h3>
</div>
<div class="abs how-step" style="left:781px;top:2606px">
  <div class="how-ring"><div class="how-inner"><svg width="40" height="40" viewBox="0 0 40 40" fill="none" stroke="#fff" stroke-width="2.4"><path d="M6 34V16h8V8h12v8h8v18Z"/><path d="M20 12v6M17 15h6M12 24h4M24 24h4M12 30h4M24 30h4M4 34h32"/></svg></div></div>
  <h3>GET A CUSTOM PLAN</h3>
</div>

<!-- testimonials -->
<h2 class="abs sec-title" style="top:2968px">CLIENT TESTIMONIALS</h2>
<div class="abs underline" style="left:561px;top:3017px"></div>
<div class="abs tcard" style="left:110px"><div class="stars">★★★★★</div><p>Lorem ipsum dolor sit amet, consectetur adipiscing elit, sed do eiusmod tempor incididunt ut labore et dolore magna aliqua ut enim ad minim veniam, quis nostrud exercitation ullamco.</p><hr><div class="person"><div class="avatar" role="img" aria-label="Client portrait photo"></div><div><b>John Smith</b><span>Florida, United States</span></div></div></div>
<div class="abs tcard" style="left:445px"><div class="stars">★★★★★</div><p>Lorem ipsum dolor sit amet, consectetur adipiscing elit, sed do eiusmod tempor incididunt ut labore et dolore magna aliqua ut enim ad minim veniam, quis nostrud exercitation ullamco.</p><hr><div class="person"><div class="avatar" role="img" aria-label="Client portrait photo"></div><div><b>John Smith</b><span>Florida, United States</span></div></div></div>
<div class="abs tcard" style="left:780px"><div class="stars">★★★★★</div><p>Lorem ipsum dolor sit amet, consectetur adipiscing elit, sed do eiusmod tempor incididunt ut labore et dolore magna aliqua ut enim ad minim veniam, quis nostrud exercitation ullamco.</p><hr><div class="person"><div class="avatar" role="img" aria-label="Client portrait photo"></div><div><b>John Smith</b><span>Florida, United States</span></div></div></div>

<!-- footer -->
<footer class="abs footer">
  <h3 class="abs f-head" style="left:98px">QUICK LINKS</h3>
  <ul class="abs links">
    <li><svg width="14" height="12" viewBox="0 0 14 12"><path d="M1 6h11M8 2l4 4-4 4" stroke="#fff" stroke-width="2" fill="none"/></svg>Home</li>
    <li><svg width="14" height="12" viewBox="0 0 14 12"><path d="M1 6h11M8 2l4 4-4 4" stroke="#fff" stroke-width="2" fill="none"/></svg>Complementary</li>
    <li><svg width="14" height="12" viewBox="0 0 14 12"><path d="M1 6h11M8 2l4 4-4 4" stroke="#fff" stroke-width="2" fill="none"/></svg>Enterprise</li>
    <li><svg width="14" height="12" viewBox="0 0 14 12"><path d="M1 6h11M8 2l4 4-4 4" stroke="#fff" stroke-width="2" fill="none"/></svg>Members</li>
    <li><svg width="14" height="12" viewBox="0 0 14 12"><path d="M1 6h11M8 2l4 4-4 4" stroke="#fff" stroke-width="2" fill="none"/></svg>Blog</li>
    <li><svg width="14" height="12" viewBox="0 0 14 12"><path d="M1 6h11M8 2l4 4-4 4" stroke="#fff" stroke-width="2" fill="none"/></svg>Contact Us</li>
  </ul>
  <div class="abs socials"><span></span><span></span><span></span><span></span></div>
  <div class="abs vline" style="left:301px"></div>
  <h3 class="abs f-head" style="left:355px">CONTACT DETAILS</h3>
  <div class="abs contact">
    <div class="ci"><div class="ci-icon"><svg width="14" height="14" viewBox="0 0 14 14" fill="#fff"><path d="M3 1l3 3-1.5 2c1 2 2 3 4 4L10.5 8.5l3 3-2 2C6 13 1 8 1 3Z"/></svg></div><div><b>Phone:</b><span>+1888 8888 8888</span></div></div>
    <div class="ci"><div class="ci-icon"><svg width="14" height="12" viewBox="0 0 14 12"><rect x="1" y="1" width="12" height="10" rx="1" fill="#fff"/><path d="M1 2l6 5 6-5" stroke="#e67e0c" stroke-width="1.6" fill="none"/></svg></div><div><b>Email:</b><span>info@companyname.in</span></div></div>
    <div class="ci"><div class="ci-icon"><svg width="12" height="16" viewBox="0 0 12 16"><path d="M6 15S1 9 1 6a5 5 0 0 1 10 0c0 3-5 9-5 9Z" fill="#fff"/><circle cx="6" cy="6" r="2" fill="#e67e0c"/></svg></div><div><b>Address:</b><span>Company Name,United State.</span></div></div>
  </div>
  <div class="abs vline" style="left:670px"></div>
  <h3 class="abs f-head" style="left:716px">CONTACT ME</h3>
  <div class="abs form">
    <div class="field">Name:</div>
    <div class="field">Email:</div>
    <div class="field">Address:</div>
    <div class="submit">Submit Now</div>
  </div>
  <div class="abs f-rule"></div>
  <p class="abs copy">Copyrights@2025.Company Name.All Rights Reserved</p>
</footer>

</body>
</html>
```